Sports hypnotherapist needs electronic letterhead design

Need a simple but classy design for a letterhead that looks good when printed. Its for a hypnotherapist who specialises in elite sport. Should have my company name and address and website details on it. I specialise in footballers.
Should look good electronically and when printed.
Include all contact details as shown in the must haves.

Target Market(s)

Sports people, elite sport.

Industry/Entity Type

Hypnotherapy

Font styles to use
Sans Serif

Colors

Designer to choose colors to be used in the design.

Requirements
Must have
• NEEDS TO BE DESIGNED IN MS WORD
• Logo +
• Calm Summit Hypnotherapists
• 27 Marlow Rise
• Wexcombe
• SN7 4LT
• Tel: 07815 264731
• E: calmsummitcoaching@examplemail.co.uk
• www: http://www.calm-summit.co.uk.
• Derek Moss
• Clinical hypnotherapist, hypnoanalyst, mental resilience coach, MSc, Dip PHH
Nice to have
• A watermark?
• Plenty of space for the A4 letter
• Prints well.
Should not have
• Too much clutter.
• Too much colour that will be costly to print.

```html
<!DOCTYPE html>
<html lang="en">
<head>
<meta charset="utf-8">
<title>Calm Summit Hypnotherapists – Letterhead</title>
<link href="https://fonts.googleapis.com/css2?family=Open+Sans:wght@400;600;700&display=swap" rel="stylesheet">
<style>
  :root {
    --ink: #222426;
    --body: #606366;
    --muted: #4a4d50;
    --accent: #5ab4e5;
    --accent-dark: #1f7fc0;
    --paper: #fafafa;
    --shade-grey: #ececec;
    --shade-blue: #eef5fb;
  }
  * { box-sizing: border-box; margin: 0; padding: 0; }
  html, body { width: 1102px; height: 1200px; overflow: hidden; background: var(--paper); }
  body { font-family: "Open Sans", sans-serif; color: var(--body); }
  .letterhead { position: relative; width: 1102px; height: 1200px; background: var(--paper); overflow: hidden; }

  .watermark {
    position: absolute; left: 45px; top: 660px; width: 533px; height: 500px;
    background: radial-gradient(ellipse at 35% 45%, var(--shade-grey) 0%, var(--shade-grey) 35%, var(--shade-blue) 60%, rgba(250,250,250,0) 78%);
    border-radius: 46% 46% 0 0;
  }

  .brand { position: absolute; left: 700px; top: 58px; display: flex; align-items: center; gap: 16px; }
  .brand-dot { width: 70px; height: 70px; border-radius: 50%; background: var(--accent); flex: none; }
  .brand-name { font-weight: 700; font-size: 44px; line-height: 46px; color: var(--ink); letter-spacing: -0.5px; }

  .letter { position: absolute; left: 109px; top: 292px; width: 882px; font-size: 15px; line-height: 22px; }
  .salutation { margin-bottom: 43px; }
  .letter p.body-copy { text-align: justify; margin-bottom: 22px; }

  .signoff { position: absolute; left: 109px; top: 818px; }
  .signoff-label { font-weight: 700; font-size: 14px; color: var(--muted); }
  .signature { width: 266px; height: 50px; margin: 10px 0 8px;
    background: linear-gradient(90deg, rgba(31,127,192,.22), rgba(31,127,192,.1)); border-radius: 25px; }
  .signoff-role { font-size: 14px; color: var(--body); }

  .contact { position: absolute; right: 41px; top: 1096px; display: flex; align-items: center; gap: 6px; font-size: 15.5px; color: var(--ink); white-space: nowrap; }
  .contact svg { width: 14px; height: 14px; fill: var(--accent); flex: none; }
  .contact span { margin-right: 6px; }
  .contact span:last-child { margin-right: 0; }

  .practitioner { position: absolute; right: 41px; top: 1128px; text-align: right; }
  .practitioner-name { font-weight: 700; font-size: 18px; color: var(--ink); line-height: 24px; }
  .practitioner-title { font-size: 12px; color: var(--ink); margin-top: 2px; }

  .footer-band { position: absolute; left: 0; bottom: 0; width: 1102px; height: 14px; background: var(--accent); }
  .footer-tab { position: absolute; left: 0; bottom: 0; width: 390px; height: 39px; background: var(--ink);
    clip-path: polygon(0 0, 360px 0, 390px 100%, 0 100%); }
  .footer-web { position: absolute; left: 109px; bottom: 10px; font-size: 15.5px; color: #fff; }
</style>
</head>
<body>
<div class="letterhead">
  <div class="watermark" role="img" aria-label="Faint watermark of a standing figure and a sprinting athlete"></div>

  <div class="brand">
    <div class="brand-dot"></div>
    <div class="brand-name">Calm<br>Summit</div>
  </div>

  <div class="letter">
    <p class="salutation">Dear Sir,</p>
    <p class="body-copy">Lorem Ipsum is simply dummy text of the printing and typesetting industry. Lorem Ipsum has been the industry's standard dummy text ever since the 1500s, when an unknown printer took a galley of type and scrambled it to make a type specimen book. It has survived not only five centuries, but also the leap into electronic typesetting, remaining essentially unchanged. It was popularised in the 1960s with the release of Letraset sheets containing Lorem Ipsum passages, and more recently with desktop publishing software like Aldus PageMaker including versions of Lorem Ipsum.</p>
    <p class="body-copy">Lorem Ipsum is simply dummy text of the printing and typesetting industry. Lorem Ipsum has been the industry's standard dummy text ever since the 1500s, when an unknown printer took a galley of type and scrambled it to make a type specimen book. It has survived not only five centuries, but also the leap into electronic typesetting, remaining essentially unchanged. It was popularised in the 1960s with the release of Letraset sheets containing Lorem Ipsum passages, and more recently with desktop publishing software like Aldus PageMaker including versions of Lorem Ipsum.</p>
    <p class="body-copy">Lorem Ipsum is simply dummy text of the printing and typesetting industry. Lorem Ipsum has been the industry's standard dummy text ever since the 1500s, when an unknown printer took a galley of type and scrambled it to make a type specimen book.</p>
  </div>

  <div class="signoff">
    <p class="signoff-label">Your Name</p>
    <div class="signature" role="img" aria-label="Handwritten signature of Martin Fells"></div>
    <p class="signoff-role">CEO &nbsp;|&nbsp; Owner</p>
  </div>

  <div class="contact">
    <svg viewBox="0 0 24 24" aria-hidden="true"><path d="M6.6 10.8a15.1 15.1 0 0 0 6.6 6.6l2.2-2.2c.3-.3.7-.4 1-.2 1.1.4 2.3.6 3.6.6.6 0 1 .4 1 1V20c0 .6-.4 1-1 1A17 17 0 0 1 3 4c0-.6.4-1 1-1h3.5c.6 0 1 .4 1 1 0 1.3.2 2.5.6 3.6.1.3 0 .7-.2 1z"/></svg>
    <span>07815 264731</span>
    <svg viewBox="0 0 24 24" aria-hidden="true"><path d="M2 5h20v14H2zM3.5 6.5 12 13l8.5-6.5v1.8L12 14.8 3.5 8.3z"/></svg>
    <span>calmsummitcoaching@examplemail.co.uk</span>
    <svg viewBox="0 0 24 24" aria-hidden="true"><path d="M12 2a7 7 0 0 0-7 7c0 5.2 7 13 7 13s7-7.8 7-13a7 7 0 0 0-7-7zm0 9.5A2.5 2.5 0 1 1 12 6.5a2.5 2.5 0 0 1 0 5z"/></svg>
    <span>27 Marlow Rise Wexcombe SN7 4LT</span>
  </div>

  <div class="practitioner">
    <p class="practitioner-name">Derek Moss</p>
    <p class="practitioner-title">Clinical Hypnotherapist, Hypnoanalyst, Mental Resilience Coach, Msc, Dip Phh</p>
  </div>

  <div class="footer-band"></div>
  <div class="footer-tab"></div>
  <p class="footer-web">www.calm-summit.co.uk</p>
</div>
</body>
</html>
```